Homemaking training schools needs a Business Card design

Designer, Hello!

No special requirements, good-looking enough.
--------------------------------------------------------------------------

Name: Marcus Dole
Chairman
Tel: 0574-71948263
Mobile: 13857420916
Email: kelvora@mailnest.example
Web: www.prt2019.example
Add: No.258, LanpingJie, BeiyuanQu, Ningbo, Zhejiang

LOGO
Ningbo PRT Homemaking Training School

Target Market(s)

pregnant women, mothers, infants, the elderly and families, including cleaning, cooking, nursing training.

Industry/Entity Type

Business

Contact Information for Business Card

Name: Marcus Dole
Chairman
Tel: 0574-71948263
Mobile: 13857420916
Email: kelvora@mailnest.example
Web: www.prt2019.example

LOGO

Font styles to use
Serif
Sans Serif
Decorative

Requirements
Nice to have
• Feels: clean, specifications, safety, comfort, warmth and happiness.

```html
<!DOCTYPE html>
<html lang="en">
<head>
<meta charset="utf-8">
<title>PingRuiTang Business Card</title>
<link rel="stylesheet" href="https://fonts.googleapis.com/css2?family=Arimo:wght@400;700&display=swap">
<style>
  :root {
    --brand-blue: #1f73bd;
    --brand-blue-deep: #175a9a;
    --brand-magenta: #d0137f;
    --brand-magenta-deep: #b80f70;
    --paper: #ffffff;
    --backdrop: #e9e6e1;
  }
  * { box-sizing: border-box; margin: 0; padding: 0; }
  html, body { width: 1200px; height: 950px; overflow: hidden; }
  body { background: var(--backdrop); font-family: "Arimo", Arial, sans-serif; }

  .stage { position: relative; width: 1200px; height: 950px; }

  .card {
    position: absolute; left: 230px; width: 740px; height: 423px;
    border-radius: 4px; overflow: hidden;
    box-shadow: 0 6px 18px rgba(0,0,0,0.18);
  }
  .card--back { top: 40px; background: linear-gradient(135deg, var(--brand-blue) 0%, var(--brand-blue-deep) 100%); }
  .card--front { top: 487px; background: var(--paper); }

  .brand-name {
    position: absolute; left: 0; right: 0; text-align: center;
    font-family: "Arimo", Arial, sans-serif; font-weight: 700;
    font-size: 54px; line-height: 1; letter-spacing: 0.5px;
  }
  .card--back .brand-name { top: 160px; color: var(--paper); }
  .card--front .brand-name { top: 100px; color: var(--brand-blue); }

  .back__web {
    position: absolute; left: 0; right: 0; top: 262px; text-align: center;
    color: rgba(255,255,255,0.85); font-size: 18px; letter-spacing: 2px;
  }

  .panel-contact {
    position: absolute; left: 0; top: 222px; width: 352px; bottom: 0;
    background: var(--brand-blue); padding: 26px 0 0 26px; color: var(--paper);
  }
  .contact-line { display: flex; align-items: center; gap: 10px; font-size: 19px; margin-bottom: 8px; white-space: nowrap; }
  .contact-line svg { width: 18px; height: 18px; flex: none; fill: var(--paper); }

  .panel-address {
    position: absolute; left: 357px; right: 0; top: 284px; bottom: 0;
    background: linear-gradient(135deg, var(--brand-magenta) 0%, var(--brand-magenta-deep) 100%);
    color: var(--paper); text-align: right; padding: 26px 30px 0 0; font-size: 18px; line-height: 1.35;
  }
  .panel-address .web { font-weight: 700; }

  .person { position: absolute; left: 357px; width: 220px; top: 228px; text-align: center; }
  .person__name { color: var(--brand-blue); font-weight: 700; font-size: 23px; }
  .person__title { color: var(--brand-magenta); font-size: 17px; margin-top: 3px; }
</style>
</head>
<body>
<main class="stage">
  <section class="card card--back" aria-label="Card back">
    <p class="brand-name">PingRuiTang</p>
    <p class="back__web">www.prt2019.example</p>
  </section>

  <section class="card card--front" aria-label="Card front">
    <p class="brand-name">PingRuiTang</p>

    <div class="person">
      <p class="person__name">Marcus Dole</p>
      <p class="person__title">Chairman</p>
    </div>

    <div class="panel-contact">
      <p class="contact-line">
        <svg viewBox="0 0 24 24" aria-hidden="true"><path d="M3 8c0-2 4-4 9-4s9 2 9 4v2h-5V8.5c-1-.5-2.5-.8-4-.8s-3 .3-4 .8V10H3zM6 12h12l2 8H4zM12 13.5a2.5 2.5 0 1 0 0 5a2.5 2.5 0 1 0 0-5z"/></svg>
        0574-71948263
      </p>
      <p class="contact-line">
        <svg viewBox="0 0 24 24" aria-hidden="true"><path d="M7 1h10a2 2 0 0 1 2 2v18a2 2 0 0 1-2 2H7a2 2 0 0 1-2-2V3a2 2 0 0 1 2-2zm0 3v14h10V4zm5 15.5a1.2 1.2 0 1 0 0 2.4a1.2 1.2 0 1 0 0-2.4z"/></svg>
        13857420916
      </p>
      <p class="contact-line">
        <svg viewBox="0 0 24 24" aria-hidden="true"><path d="M2 5h20v14H2zm2 2v.5l8 5.5l8-5.5V7zm0 3v7h16v-7l-8 5.5z"/></svg>
        kelvora@mailnest.example
      </p>
    </div>

    <div class="panel-address">
      <p>No.258, LanpingJie</p>
      <p>BeiyuanQu, Ningbo, Zhejiang</p>
      <p class="web">www.prt2019.example</p>
    </div>
  </section>
</main>
</body>
</html>
```